Modern Social Media Ad for Law Firm

We need a crisp ad for social media for our law firm, The Harlow Group. The ad will adverrtise for car accident and personal injury cases. Our website is rightsideclaims.example. Our phoone number is 555-314-8826. Use a photo of of our building in the background. I want the add to be light and cripsy. Use logo and photo of attorney. Our address is 418 North Birch Avenue at Red Finch Ballpark.

Target Market(s)

We want to car accident cases and injury cases. The ad should say "Car Accident or Injury? Call us." No fee unless we win!

Industry/Entity Type

Legal

Requirements
Must have
• large photo of me. white background. maybe grayed out columns in the background. website at the bottom with phone number. The Harlow Group logo and name at top. Our colors are black and gold with red as an accent color. Should say "Pensacola, FL" at the bottom in small print.
Nice to have
• if you could fade our building into the background that woul dbe nice
Should not have
• no scales of justice -- I want it to be clean, white, crisp, modern

```html
<!DOCTYPE html>
<html lang="en">
<head>
<meta charset="utf-8">
<title>The Harlow Group – Car Accident or Injury</title>
<link rel="stylesheet" href="https://fonts.googleapis.com/css2?family=Anton&family=Cinzel:wght@600&family=Exo+2:ital,wght@1,900&family=Michroma&family=Saira+Condensed:wght@500&family=Roboto:wght@500&display=swap">
<style>
  :root {
    --ink: #000000;
    --gold: #d89a2b;
    --paper: #ffffff;
    --sepia-light: #e9dcc4;
    --sepia-mid: #c9b48f;
    --suit-light: #8a8f96;
    --suit-dark: #4b5058;
  }
  * { margin: 0; padding: 0; box-sizing: border-box; }
  html, body { width: 1200px; height: 1200px; overflow: hidden; background: var(--paper); }
  .ad { position: relative; width: 1200px; height: 1200px; overflow: hidden; background: var(--paper); }

  .building-photo { position: absolute; left: 354px; top: 0; width: 846px; height: 345px; }

  .brand { position: absolute; left: 60px; top: 20px; width: 272px; text-align: center; }
  .brand-mark { display: block; width: 110px; height: 110px; margin: 70px auto 60px; background: var(--gold); }
  .brand-name { font-family: "Cinzel", serif; font-weight: 600; font-size: 19px; color: var(--ink); letter-spacing: 0.5px; white-space: nowrap; }
  .brand-sub { display: flex; align-items: center; gap: 6px; margin-top: 0; font-family: "Roboto", sans-serif; font-weight: 500; font-size: 12.5px; color: var(--ink); }
  .brand-sub::before, .brand-sub::after { content: ""; flex: 1; height: 1px; background: #555; }

  .headline { position: absolute; left: 40px; width: 610px; text-align: center;
    font-family: "Anton", sans-serif; color: var(--ink); text-transform: none;
    -webkit-text-stroke: 6px var(--gold); paint-order: stroke fill; line-height: 1; }
  .headline-question { top: 362px; font-size: 92px; line-height: 88px; }
  .headline-offer { top: 588px; font-size: 84px; line-height: 79px; }

  .phone { position: absolute; left: 64px; top: 928px; width: 548px; text-align: center;
    font-family: "Exo 2", sans-serif; font-style: italic; font-weight: 900; font-size: 70px; color: var(--ink); letter-spacing: 1px; }

  .footer-band { position: absolute; left: 0; top: 1022px; width: 1200px; height: 178px; background: var(--ink); }
  .footer-info { position: absolute; left: 40px; top: 1036px; width: 610px; text-align: center; }
  .city { font-family: "Michroma", sans-serif; font-size: 24px; color: var(--paper); font-weight: 700; letter-spacing: 1px; }
  .website { font-family: "Saira Condensed", sans-serif; font-weight: 500; font-size: 50px; color: var(--gold); line-height: 1.1; margin-top: 6px; }
  .address { font-family: "Saira Condensed", sans-serif; font-weight: 500; font-size: 29px; color: var(--gold); line-height: 1.1; margin-top: 4px; }

  .attorney-photo { position: absolute; left: 590px; top: 25px; width: 610px; height: 1175px; }
</style>
</head>
<body>
<main class="ad">
  <svg class="building-photo" role="img" aria-label="Sepia photo of the firm's office building fading into the white background" viewBox="0 0 846 345">
    <defs>
      <linearGradient id="buildingTone" x1="0" y1="0" x2="0" y2="1">
        <stop offset="0" stop-color="var(--sepia-light)"/>
        <stop offset="1" stop-color="var(--sepia-mid)"/>
      </linearGradient>
      <linearGradient id="fadeX" x1="0" y1="0" x2="1" y2="0">
        <stop offset="0" stop-color="#fff" stop-opacity="0"/>
        <stop offset="0.25" stop-color="#fff" stop-opacity="1"/>
      </linearGradient>
      <linearGradient id="fadeY" x1="0" y1="0" x2="0" y2="1">
        <stop offset="0.7" stop-color="#fff" stop-opacity="1"/>
        <stop offset="1" stop-color="#fff" stop-opacity="0"/>
      </linearGradient>
      <mask id="buildingFade">
        <rect width="846" height="345" fill="url(#fadeX)"/>
      </mask>
      <mask id="buildingFadeY">
        <rect width="846" height="345" fill="url(#fadeY)"/>
      </mask>
    </defs>
    <g mask="url(#buildingFadeY)">
      <rect width="846" height="345" fill="url(#buildingTone)" mask="url(#buildingFade)"/>
    </g>
  </svg>

  <header class="brand">
    <span class="brand-mark"></span>
    <div class="brand-name">The Harlow Group, PLLC.</div>
    <div class="brand-sub">Attorneys At Law</div>
  </header>

  <h1 class="headline headline-question">Car Accident<br>or Injury?</h1>
  <p class="headline headline-offer">Call us.<br>No fee unless<br>we win!</p>

  <p class="phone">555-314-8826</p>

  <div class="footer-band"></div>
  <footer class="footer-info">
    <div class="city">PENSACOLA, FL</div>
    <div class="website">rightsideclaims.example</div>
    <div class="address">418 North Birch Avenue at Red Finch Ballpark.</div>
  </footer>

  <svg class="attorney-photo" role="img" aria-label="Photo of the attorney in a gray suit and teal tie, arms crossed" viewBox="0 0 610 1175">
    <defs>
      <linearGradient id="suitTone" x1="0" y1="0" x2="1" y2="1">
        <stop offset="0" stop-color="var(--suit-light)"/>
        <stop offset="1" stop-color="var(--suit-dark)"/>
      </linearGradient>
    </defs>
    <path d="M230 0 H470 V280 L590 330 L610 360 V1175 H50 L20 1040 L0 650 L20 420 L150 320 L230 280 Z" fill="url(#suitTone)"/>
  </svg>
</main>
</body>
</html>
```